Letterhead for Conveyancing Company

Use existing logo to create a letterhead for a conveyancing company. Must be able to be used in Microsoft Word. Easy to read and professional.
Contact information to be at the bottom.
Bright Oak Conveyancing Pty Ltd
ACN 621 984 736PO Box 535 Campbelltown SA 5074
Mobile - 0461739286
Web address - www.brightoakconveyancing.com.au

Requirements
Must have
• Logo and contact details.
• Simple and professional.

```html
<!DOCTYPE html>
<html lang="en">
<head>
<meta charset="utf-8">
<title>Bright Oak Conveyancing – Letterhead</title>
<link href="https://fonts.googleapis.com/css2?family=Arimo:wght@400;700&family=Cormorant+SC:wght@500&display=swap" rel="stylesheet">
<style>
  :root {
    --pink: #e6379a;
    --grey: #8e8e8e;
    --grey-light: #b4b4b4;
    --ink: #6f6f6f;
    --paper: #ffffff;
    --stage: #d9dcde;
  }
  * { box-sizing: border-box; margin: 0; padding: 0; }
  html, body { width: 1200px; height: 784px; overflow: hidden; background: var(--stage); }
  body { font-family: "Arimo", Arial, sans-serif; }

  .letterhead {
    position: absolute; left: 338px; top: 22px;
    width: 524px; height: 740px;
    background: var(--paper);
    box-shadow: 0 2px 10px rgba(0,0,0,.12);
  }

  .edge-stub { position: absolute; top: 0; width: 4px; height: 44px; }
  .edge-stub--left { left: 0; }
  .edge-stub--right { right: 0; }
  .edge-stub::before, .edge-stub::after { content: ""; position: absolute; left: 0; width: 100%; height: 22px; }
  .edge-stub::before { top: 0; background: var(--pink); }
  .edge-stub::after { top: 22px; background: var(--grey-light); }

  .brand {
    position: absolute; top: 44px; right: 46px;
    display: flex; align-items: center; gap: 8px;
    font-weight: 700; font-size: 19px; line-height: 1.05;
    color: var(--pink); text-align: right;
  }
  .brand__mark { width: 12px; height: 12px; border-radius: 50%; background: var(--pink); }

  .letter-body {
    position: absolute; left: 52px; top: 104px; width: 420px;
    font-size: 8.4px; line-height: 1.55; color: var(--ink);
  }
  .letter-body p { margin-bottom: 11px; }

  .signature {
    position: absolute; left: 56px; top: 492px;
    width: 150px; height: 40px;
    background: linear-gradient(90deg, rgba(120,120,120,.18), rgba(120,120,120,.05));
    border-radius: 3px;
  }

  .footer { position: absolute; left: 0; right: 0; bottom: 0; }
  .footer__name {
    font-family: "Cormorant SC", Georgia, serif; font-weight: 500;
    color: var(--pink); font-size: 15px; letter-spacing: .5px;
    text-align: center; margin-bottom: 5px;
  }
  .footer__rule { display: flex; justify-content: center; margin-bottom: 8px; }
  .footer__rule span { height: 3px; width: 100px; }
  .footer__rule .pink { background: var(--pink); }
  .footer__rule .grey { background: var(--grey-light); width: 70px; }
  .footer__line { height: 1px; background: var(--grey-light); margin: 0 8px 5px; }
  .contact-row {
    display: flex; justify-content: center; flex-wrap: nowrap; gap: 8px;
    font-size: 6.4px; color: var(--ink); padding: 0 8px 8px;
  }
  .contact-row li { list-style: none; display: flex; align-items: center; gap: 3px; white-space: nowrap; }
  .contact-row svg { width: 7px; height: 7px; }
  .footer__band { display: flex; height: 7px; }
  .footer__band .pink { flex: 0 0 56%; background: var(--pink); }
  .footer__band .grey { flex: 1; background: var(--grey-light); }
</style>
</head>
<body>
<main class="letterhead">
  <div class="edge-stub edge-stub--left"></div>
  <div class="edge-stub edge-stub--right"></div>

  <header class="brand">
    <span class="brand__mark"></span>
    <span>Bright Oak<br>Conveyancing</span>
  </header>

  <section class="letter-body">
    <p>Lorem Ipsum is simply dummy text of the printing and typesetting industry. Lorem Ipsum has been the industry's standard dummy text ever since the 1500s, when an unknown printer took a galley of type and scrambled it to make a type specimen book. It has survived not only five centuries, but also the leap into electronic typesetting, remaining essentially unchanged. It was popularised in the 1960s with the release of sheets containing Lorem Ipsum passages, and more recently with desktop publishing software including versions of Lorem Ipsum.</p>
    <p>It is a long established fact that a reader will be distracted by the readable content of a page when looking at its layout. The point of using Lorem Ipsum is that it has a more-or-less normal distribution of letters, as opposed to using 'Content here, content here', making it look like readable English. Many desktop publishing packages and web page editors now use Lorem Ipsum as their default model text, and a search for 'lorem ipsum' will uncover many web sites still in their infancy. Various versions have evolved over the years, sometimes by accident, sometimes on purpose (injected humour and the like).</p>
    <p>Contrary to popular belief, Lorem Ipsum is not simply random text. It has roots in a piece of classical Latin literature from 45 BC, making it over 2000 years old. Daniel Whitcombe, a Latin professor at a college in Virginia, looked up one of the more obscure Latin words, consectetur, from a Lorem Ipsum passage, and going through the cites of the word in classical literature, discovered the undoubtable source. Lorem Ipsum comes from sections 1.10.32 and 1.10.33 of "de Finibus Bonorum et Malorum". The generated Lorem Ipsum is therefore always free from repetition, injected humour, or non-characteristic words etc.</p>
  </section>

  <div class="signature" role="img" aria-label="Handwritten signature"></div>

  <footer class="footer">
    <p class="footer__name">Bright Oak Conveyancing Pty Ltd</p>
    <div class="footer__rule"><span class="pink"></span><span class="grey"></span></div>
    <div class="footer__line"></div>
    <ul class="contact-row">
      <li><svg viewBox="0 0 10 10"><circle cx="5" cy="5" r="5" fill="var(--pink)"/><path d="M5 2.2a1.9 1.9 0 0 0-1.9 1.9C3.1 5.5 5 7.8 5 7.8s1.9-2.3 1.9-3.7A1.9 1.9 0 0 0 5 2.2z" fill="#fff"/></svg>PO Box 871 Marlowdale SA 5096</li>
      <li><svg viewBox="0 0 10 10"><circle cx="5" cy="5" r="5" fill="var(--pink)"/><rect x="3.5" y="2.2" width="3" height="5.6" rx=".6" fill="#fff"/></svg>0461739286</li>
      <li><svg viewBox="0 0 10 10"><circle cx="5" cy="5" r="5" fill="var(--pink)"/><rect x="2.5" y="3.2" width="5" height="3.6" fill="#fff"/><path d="M2.5 3.2 5 5.2l2.5-2" stroke="var(--pink)" stroke-width=".6" fill="none"/></svg>contact@brightoakconveyancing.com.au</li>
      <li><svg viewBox="0 0 10 10"><circle cx="5" cy="5" r="5" fill="var(--pink)"/><circle cx="5" cy="5" r="2.4" fill="none" stroke="#fff" stroke-width=".7"/></svg>www.brightoakconveyancing.com.au</li>
      <li><svg viewBox="0 0 10 10"><circle cx="5" cy="5" r="5" fill="var(--pink)"/></svg>ACN 583 217 469</li>
    </ul>
    <div class="footer__band"><span class="pink"></span><span class="grey"></span></div>
  </footer>
</main>
</body>
</html>
```